Antiseptic products for Verolin East Africa

I need several antiseptic product designs for topical solutions such as surgical spirit, methylated spirit, hand sanitizer, calamine lotion, povidone solution, glycerine, povidone mouthwash, chlorhexidine solution, and sodium hypochlorite solution.

KINDLY START WITH THE HAND SANITIZER DESIGN, URGENT.

Target Market(s)

International market

Industry/Entity Type

Pharmaceutical

Font styles to use
Serif
Script

Colors
33a6d7
3277b5
0758a5
7651a1
886aae
e34197
e667a6
f78f20

Requirements
Must have
• Elegant designs, writtings to appear as they are. safety symbols to appear such as flammable or corrosive.
Nice to have
• Attractive colours but keep it simple and classy.

```html
<!DOCTYPE html>
<html lang="en">
<head>
<meta charset="utf-8">
<title>Verolin East Africa – Antiseptic Labels</title>
<link href="https://fonts.googleapis.com/css2?family=Encode+Sans+Semi+Condensed:wght@600;700&family=Fira+Sans+Condensed:wght@500;600&family=Montserrat:wght@400;500;600;700;800&family=Open+Sans:wght@400;600&display=swap" rel="stylesheet">
<style>
  :root{
    --bg:#f1f1f2;
    --violet-light:#8f74b5;
    --violet-dark:#6e4e99;
    --violet-ink:#8a3ea3;
    --gold-light:#daa843;
    --gold-dark:#c38a24;
    --gold-pill:#8b5f17;
    --gold-ink:#6d4a10;
    --paper:#f4f4f4;
    --ink:#4a4a4a;
    --logo-blue:#3277b5;
    --white:#ffffff;
  }
  *{margin:0;padding:0;box-sizing:border-box}
  html,body{width:1200px;height:1200px;overflow:hidden}
  body{
    background:radial-gradient(circle at 50% 45%,#ffffff 0%,var(--bg) 70%,#e4e4e6 100%);
    font-family:"Open Sans",sans-serif;
    position:relative;
  }
  .label{
    position:absolute;top:230px;width:340px;height:740px;
    border-radius:14px;overflow:hidden;
    box-shadow:0 10px 30px rgba(0,0,0,.12);
  }
  .label--violet{left:190px;background:linear-gradient(135deg,var(--violet-light),var(--violet-dark))}
  .label--gold{left:670px;background:linear-gradient(135deg,var(--gold-light),var(--gold-dark))}
  .abs{position:absolute}
  .center{left:0;right:0;text-align:center}

  .brand-mark{top:84px}
  .brand-mark__name{font-family:"Montserrat",sans-serif;font-weight:700;font-size:25px;color:var(--white);letter-spacing:.5px}
  .brand-mark__region{font-family:"Montserrat",sans-serif;font-weight:400;font-size:10.5px;letter-spacing:5px;color:var(--white);margin-top:6px}

  .product-title{font-family:"Encode Sans Semi Condensed",sans-serif;font-weight:700;color:#f2f2f2;font-size:54px;letter-spacing:-1px;top:200px}
  .product-strength{font-family:"Encode Sans Semi Condensed",sans-serif;font-weight:600;color:#f2f2f2;font-size:29px;top:266px}

  .paper-panel{left:0;top:0;width:340px;height:740px}

  .seal{left:241px;top:310px;width:80px;height:80px;border-radius:50%;background:var(--violet-dark);border:3px solid #b8a3d2}

  .claim-title{left:12px;top:404px;font-family:"Montserrat",sans-serif;font-weight:700;font-size:27px;color:var(--violet-ink);letter-spacing:-.8px}
  .info-block{left:10px;top:446px;width:190px;font-family:"Montserrat",sans-serif;color:var(--ink)}
  .info-block .rule{border-bottom:1px solid #777;padding:3px 0 4px;font-size:12px;line-height:1.3}
  .info-block .rule b{font-weight:600}
  .info-block .caps{text-transform:uppercase;letter-spacing:.2px}

  .bubbles{left:0;width:340px}

  .volume{width:58px;height:58px;border-radius:50%;border:2.5px solid var(--white);color:var(--white);font-family:"Montserrat",sans-serif;font-weight:700;font-size:19px;line-height:.95;text-align:center;padding-top:9px}
  .volume small{display:block;font-size:19px}
  .label--violet .volume{left:268px;top:549px;background:var(--violet-dark)}
  .label--gold .volume{left:256px;top:555px;background:var(--gold-dark)}

  .cert-mark{width:18px;height:30px;border-radius:3px;border:2px solid var(--logo-blue);background:var(--white)}
  .label--violet .cert-mark{left:310px;top:628px}
  .label--gold .cert-mark{left:310px;top:620px}

  .batch{left:10px;top:648px;font-size:11px;line-height:21px;color:#555}
  .maker{right:12px;top:680px;text-align:right;font-size:11px;color:#444;line-height:16px}
  .maker b{font-family:"Montserrat",sans-serif;font-weight:700}

  .gold-title{font-family:"Montserrat",sans-serif;font-weight:700;color:#f6f6f6;font-size:50px;line-height:52px;top:176px;letter-spacing:-1px}
  .gold-pill{left:22px;width:296px;top:297px;height:32px;border-radius:16px;background:var(--gold-pill);color:#f6f6f6;font-family:"Fira Sans Condensed",sans-serif;font-weight:600;font-size:24px;line-height:32px;text-align:center}
  .gold-pill span{font-weight:500}
  .gold-strength{top:332px;font-family:"Montserrat",sans-serif;font-weight:400;color:#f6f6f6;font-size:28px}
  .benefits{left:15px;top:383px;font-family:"Fira Sans Condensed",sans-serif;font-weight:600;color:#f6f6f6;font-size:25px;line-height:28px}
  .kill-badge{left:232px;top:362px;width:86px;height:86px;border-radius:50%;background:#3a2a10;border:2px solid #7b5b1f;color:var(--gold-light);font-family:"Fira Sans Condensed",sans-serif;font-weight:600;text-align:center;font-size:10px;line-height:1.1;padding-top:16px}
  .kill-badge strong{display:block;background:var(--gold-light);color:#2b1f0a;font-size:13px;margin:4px -10px;padding:1px 0;transform:rotate(8deg)}
  .divider{left:15px;top:470px;width:280px;border-top:1px solid #f3e2bf}
  .directions{left:15px;top:478px;width:292px;color:#fff;font-size:10.5px;line-height:13px}
  .directions h4{font-family:"Montserrat",sans-serif;font-weight:600;font-size:11.5px;margin-top:3px}
</style>
</head>
<body>

<!-- Gentian Violet label -->
<section class="label label--violet" aria-label="Gentian Violet label">
  <svg class="abs paper-panel" viewBox="0 0 340 740" aria-hidden="true">
    <path d="M0 378 Q170 268 340 378 L340 740 L0 740 Z" fill="var(--paper)"/>
    <path d="M0 372 Q170 262 340 372" fill="none" stroke="#8a3ea3" stroke-width="6"/>
  </svg>

  <div class="abs center brand-mark">
    <div class="brand-mark__name">verolin</div>
    <div class="brand-mark__region">EAST AFRICA</div>
  </div>

  <h1 class="abs center product-title">Gentian Violet</h1>
  <p class="abs center product-strength">1% solution</p>

  <div class="abs seal" role="img" aria-label="Quality seal"></div>

  <h2 class="abs claim-title">FIRST AID ANTISEPIC</h2>
  <div class="abs info-block">
    <div class="rule caps"><b>For external use only</b></div>
    <div class="rule caps"><b>Caution:</b><br>Keep out of<br>reach of children</div>
    <div class="rule"><b>STORAGE:</b><br>Store in a cool dry place</div>
  </div>

  <svg class="abs bubbles" style="top:560px;height:180px" viewBox="0 0 340 180" role="img" aria-label="Bubble pattern band">
    <path d="M0 30 Q60 5 120 28 T240 22 T340 20 L340 180 L0 180 Z" fill="var(--violet-dark)"/>
  </svg>
  <div class="abs volume">200<small>mL</small></div>
  <div class="abs cert-mark" role="img" aria-label="Standards mark"></div>

  <div class="abs batch">B. No:<br>Mfg date:<br>Exp date:</div>
  <div class="abs maker" style="color:#fff">Manufacturing by:<br><b>Kalani Works Ltd.</b> | 4470 - 20100 Kenya</div>
</section>

<!-- Povidone Iodine label -->
<section class="label label--gold" aria-label="Povidone Iodine label">
  <svg class="abs bubbles" style="top:560px;height:180px" viewBox="0 0 340 180" role="img" aria-label="Bubble pattern band">
    <path d="M0 40 Q60 15 120 36 T240 30 T340 28 L340 180 L0 180 Z" fill="var(--paper)"/>
  </svg>

  <div class="abs center brand-mark" style="top:72px">
    <div class="brand-mark__name">verolin</div>
    <div class="brand-mark__region">EAST AFRICA</div>
  </div>

  <h1 class="abs center gold-title">POVIDONE<br>IODINE</h1>
  <div class="abs gold-pill">Gangle <span>&amp;</span> Mouthwash</div>
  <p class="abs center gold-strength">1% oral solution</p>

  <div class="abs benefits">Kills Gems<br>Stops Mouth Odour<br>Sootnes Sove Throats</div>
  <div class="abs kill-badge">VIRUSES<strong>ELIMINATES 99%</strong>BACTERIA</div>

  <div class="abs divider"></div>
  <div class="abs directions">
    <h4>Directions:</h4>
    Use full strength as a gargle or mouthwash. May be diluted with an equal volume of water. Gargle for at least 30 seconds every 2-4 hrs or as directed.
    <h4>Contain dications:</h4>
    Sensitivity to iodine, hyperthyroid idioms
  </div>

  <div class="abs volume">200<small>mL</small></div>
  <div class="abs cert-mark" role="img" aria-label="Standards mark"></div>

  <div class="abs batch">B. No:<br>Mfg date:<br>Exp date:</div>
  <div class="abs maker">Manufacturing by:<br><b>Kalani Works Ltd.</b> | 4470 - 20100 Kenya</div>
</section>

</body>
</html>
```